A design led business card for the construction industry

High-end business card to match logo. White logo on dark grey/off black to the front. Matching dark font on white to back, possibly with logo design again.

We offer construction and project management services to commercial and private clients in the UK. Projetcs range from newbuilds, conversion of listed buildings and refurbishments and extensions of existing homes. Our focus is on quality and attention to detail using the highest skills.

Contact Information for Business Card

Name; Dorian Keble BSc
Position; Project Manager
Mobile; 07962 408 175
Tel; 01632 960457
email; dorian@stonevale.co.uk
web; www.stonevale.co.uk
Address; Ashcombe on Wyre, KX4 7PW

Colors

Designer to choose only greyscale colors for use in the design.

Requirements
Must have
• To include the below description of the business,

CONSTRUCTION - PROJECT MANAGEMENT
Nice to have
• The posibility of the top back of the card being used as a ruler. So will have a measurement to scale in mm or an architect scale of 1:50
Should not have
• Should not be portrait

```html
<!DOCTYPE html>
<html lang="en">
<head>
<meta charset="utf-8">
<title>Stonevale — Business Card</title>
<link href="https://fonts.googleapis.com/css2?family=Arimo:wght@400;700&display=swap" rel="stylesheet">
<style>
  :root {
    --backdrop: #0c0c0d;
    --card-front: #2b2b2c;
    --card-back: #252526;
    --ink-white: #f4f4f4;
    --ink-soft: #d9d9d9;
    --ink-emboss: #77777a;
    --rule: #58585a;
  }
  * { margin: 0; padding: 0; box-sizing: border-box; }
  html, body {
    width: 1200px; height: 820px; overflow: hidden;
    background: var(--backdrop);
    font-family: "Arimo", Arial, sans-serif;
  }
  .stage {
    width: 1200px; height: 820px;
    display: flex; align-items: center; justify-content: center; gap: 40px;
  }
  .card {
    width: 540px; height: 350px; position: relative;
    border-radius: 2px;
  }
  /* Contact side */
  .card--contact { background: var(--card-front); color: var(--ink-white); }
  .brand {
    position: absolute; left: 44px; top: 0; bottom: 0; width: 220px;
    display: flex; flex-direction: column; align-items: center; justify-content: center; gap: 22px;
  }
  .brand__mark { width: 26px; height: 26px; border: 2px solid var(--ink-white); }
  .brand__name {
    font-size: 22px; font-weight: 400; letter-spacing: 9px; color: var(--ink-white);
    padding-left: 9px;
  }
  .divider {
    position: absolute; left: 286px; top: 110px; width: 1px; height: 140px; background: var(--rule);
  }
  .contact { position: absolute; left: 308px; top: 104px; }
  .contact__name { font-size: 17px; font-weight: 700; letter-spacing: 0.3px; }
  .contact__name span { font-weight: 400; }
  .contact__role { font-size: 13px; color: var(--ink-soft); margin-top: 2px; }
  .contact__list { list-style: none; margin-top: 14px; }
  .contact__list li {
    display: flex; align-items: center; gap: 7px;
    font-size: 13.5px; line-height: 18px; color: var(--ink-white);
  }
  .contact__list svg { width: 12px; height: 12px; flex: none; }
  .contact__address { font-size: 13.5px; margin-top: 14px; color: var(--ink-white); }

  /* Brand side */
  .card--brand { background: var(--card-back); }
  .brand-feature {
    position: absolute; left: 0; right: 0; top: 96px;
    display: flex; flex-direction: column; align-items: center; gap: 26px;
  }
  .brand-feature__mark { width: 56px; height: 56px; border: 3px solid var(--ink-emboss); }
  .brand-feature__name {
    font-size: 34px; letter-spacing: 14px; color: var(--ink-emboss); padding-left: 14px;
  }
  .tagline {
    position: absolute; left: 0; right: 0; bottom: 58px; text-align: center;
    font-size: 14px; letter-spacing: 1.2px; color: var(--ink-emboss);
  }
</style>
</head>
<body>
<main class="stage">
  <section class="card card--contact" aria-label="Contact side">
    <div class="brand">
      <div class="brand__mark"></div>
      <div class="brand__name">STONEVALE</div>
    </div>
    <div class="divider"></div>
    <div class="contact">
      <p class="contact__name">DORIAN KEBLE <span>BSc</span></p>
      <p class="contact__role">Project Manager</p>
      <ul class="contact__list">
        <li><svg viewBox="0 0 12 12" fill="none" stroke="#f4f4f4" stroke-width="1.2"><rect x="3" y="0.8" width="6" height="10.4" rx="1"/><line x1="5" y1="9.4" x2="7" y2="9.4"/></svg>07962 408 175</li>
        <li><svg viewBox="0 0 12 12" fill="#f4f4f4"><path d="M2.4 1 4.3 3 3.4 4.3c.7 1.6 2 2.9 3.6 3.6L8.3 7l2 1.9-1.3 2C5 10.6 1.4 7 1.1 2.3z"/></svg>01632 960457</li>
        <li><svg viewBox="0 0 12 12" fill="none" stroke="#f4f4f4" stroke-width="1.2"><rect x="0.8" y="2.5" width="10.4" height="7.2"/><path d="M0.8 2.5 6 6.6l5.2-4.1"/></svg>dorian@stonevale.co.uk</li>
        <li><svg viewBox="0 0 12 12" fill="none" stroke="#f4f4f4" stroke-width="1"><circle cx="6" cy="6" r="5"/><ellipse cx="6" cy="6" rx="2.2" ry="5"/><line x1="1" y1="6" x2="11" y2="6"/></svg>www.stonevale.co.uk</li>
      </ul>
      <p class="contact__address">Ashcombe on Wyre, KX4 7PW</p>
    </div>
  </section>

  <section class="card card--brand" aria-label="Brand side">
    <div class="brand-feature">
      <div class="brand-feature__mark"></div>
      <div class="brand-feature__name">STONEVALE</div>
    </div>
    <p class="tagline">CONSTRUCTION - PROJECT MANAGEMENT</p>
  </section>
</main>
</body>
</html>
```